tinyTally Resource Book - 10 maths tasks to do outside

I need a 22 (11 pages back to back) page A6 sized book produced to standard for submission to professional printer. Needs to be as .pdf file showing guide lines and allowances for colour bleed. I have text already written and submitted as attachment in a Word file with margins set to A6 size. The theme of the materials is "Nature Play" so using lots of pictures from nature (Australia preferably) and showing lots of patterns in nature (rocks, leaves, flower petals etc). Some of the tasks refer to specific activities, such as "shadows" and "floating" so would be great to illustrate appropriately. The big emphasis is on learning outside the classroom, getting kids to engage actively with nature. I would like to see the pages as full colour - so not white background. The book itself will be spiral bound along the top edge so a margin of at least 1cm will be required at the top of each page (or the bottom of even numbered pages). Book will be printed on plastic laminated matte paper for outdoor use. Font size needs to be big enough to read. Fonts sizes, alignments and page numbers are all different at the moment and need to be standardised. One photo is included in a page as a sample if you can use it, otherwise disregard. Logo for Wattlebrook Numeracy Guild is also included to have as part of the acknowledgements at the back of the book.

Target Market(s)

Book is for early childhood and preschool teachers.

Industry/Entity Type

Education

Font styles to use
Sans Serif

Requirements
Must have
• Colour and appeal.
Nice to have
• Use of natural colours instead of bright catchy colours but that is your call.
Should not have
• American spelling

```html
<!DOCTYPE html>
<html lang="en-AU">
<head>
<meta charset="utf-8">
<title>tinyTally – 7. Make a Star</title>
<link href="https://fonts.googleapis.com/css2?family=Jost:ital,wght@0,400;0,700;0,800;1,700&display=swap" rel="stylesheet">
<style>
  :root {
    --paper: #ffffff;
    --navy: #2e3a8c;
    --star-blue: #36449a;
    --ink: #2b2b2b;
    --bullet-red: #d8232a;
    --sea-top: #7fb3c9;
    --sea-mid: #c9dde3;
    --sand-light: #e6ddcf;
    --sand-mid: #cfc2ae;
    --sand-deep: #b9aa94;
    --crop: #222222;
  }
  * { margin: 0; padding: 0; box-sizing: border-box; }
  html, body { width: 902px; height: 1200px; overflow: hidden; background: var(--paper); }
  .page { position: relative; width: 902px; height: 1200px; font-family: "Jost", sans-serif; }
  .crop-marks { position: absolute; inset: 0; }
  .nature-backdrop {
    position: absolute; left: 54px; top: 52px; width: 796px; height: 1094px;
    background: linear-gradient(180deg, var(--sea-top) 0%, var(--sea-mid) 14%, var(--sand-light) 30%, var(--sand-mid) 62%, var(--sand-deep) 100%);
  }
  .task-title {
    position: absolute; left: 0; width: 902px; top: 104px; text-align: center;
    font-weight: 800; font-size: 44px; color: var(--navy);
    text-shadow: 2px 2px 0 #fff, -2px -2px 0 #fff, 2px -2px 0 #fff, -2px 2px 0 #fff;
  }
  .outcome {
    position: absolute; left: 0; width: 902px; top: 180px; text-align: center;
    font-weight: 700; font-size: 29px; line-height: 44px; color: var(--navy);
  }
  .lead {
    position: absolute; left: 126px; width: 650px;
    font-weight: 700; font-style: italic; font-size: 24px; line-height: 36px; color: var(--navy);
  }
  .lead.dispositions { top: 284px; }
  .lead.educators { top: 520px; }
  .lead.opportunity { top: 646px; }
  .detail {
    position: absolute; left: 198px; width: 580px;
    font-weight: 400; font-size: 32px; line-height: 46px; color: var(--ink);
  }
  .detail.play { top: 432px; }
  .detail.environments { top: 558px; }
  .opportunities { position: absolute; left: 186px; top: 684px; list-style: none; }
  .opportunities li {
    position: relative; padding-left: 34px; width: 360px;
    font-size: 29px; line-height: 42px; color: var(--ink);
  }
  .opportunities li::before {
    content: ""; position: absolute; left: 4px; top: 12px; width: 16px; height: 16px;
    background: var(--bullet-red); transform: rotate(45deg);
  }
  .star { position: absolute; left: 0; top: 0; }
</style>
</head>
<body>
<div class="page">
  <div class="nature-backdrop" role="img" aria-label="Photograph of smooth beach pebbles with the sea softly blurred behind"></div>

  <svg class="crop-marks" width="902" height="1200" viewBox="0 0 902 1200" aria-hidden="true">
    <g stroke="var(--crop)" stroke-width="1" fill="none">
      <line x1="54" y1="0" x2="54" y2="34"/><line x1="0" y1="52" x2="34" y2="52"/>
      <polyline points="36,74 74,74 74,36"/>
      <line x1="850" y1="0" x2="850" y2="34"/><line x1="868" y1="52" x2="902" y2="52"/>
      <polyline points="866,74 828,74 828,36"/>
      <line x1="54" y1="1166" x2="54" y2="1200"/><line x1="0" y1="1146" x2="34" y2="1146"/>
      <polyline points="36,1126 74,1126 74,1164"/>
      <line x1="850" y1="1166" x2="850" y2="1200"/><line x1="868" y1="1146" x2="902" y2="1146"/>
      <polyline points="866,1126 828,1126 828,1164"/>
    </g>
  </svg>

  <h1 class="task-title">7. Make a Star</h1>
  <h2 class="outcome">EYLF – Outcome 4: Children are<br>confident and involved learners</h2>

  <p class="lead dispositions">Children develop dispositions for learning such as curiosity, cooperation, confidence, creativity, commitment, enthusiasm, persistence, imagina-<br>tion and reflexivity when they...</p>
  <p class="detail play">use play to investigate, imagine and explore ideas</p>

  <p class="lead educators">Educators promote this learning when they...</p>
  <p class="detail environments">provide learning environments that are flexible and open-ended</p>

  <p class="lead opportunity">This task provides an opportunity to:</p>
  <ul class="opportunities">
    <li>explore the concept of “alternating turns”</li>
    <li>share and cooperate to produce a star</li>
    <li>explore concept of repeated addition</li>
    <li>develop awareness of radial symmetry</li>
  </ul>

  <svg class="star" width="902" height="1200" viewBox="0 0 902 1200" aria-hidden="true">
    <polygon fill="var(--star-blue)"
      points="682,772 713,884 818,878 736,943 766,1053 681,985 596,1054 628,943 544,880 651,884"/>
  </svg>
</div>
</body>
</html>
```